Trifold Total Body Wellness pamphlet for dental patients

I had Chat GPT help create and layout a pamphlet to be used in my dental office. I placed the wording and would like a graphic designer to make it better so I can get it printed and start handing it out to patients. We are a science driven dental office with the goal of total body wellness. Our main colors our black, white and gray with red as an accent color. We like a modern and clean look. We are an established dental practice and would like to evolve the way we do things when science shows a better way. This pamphlet will help explain to our existing patients why we are doing things differently and how it will better help us treat the disease in their mouths.

```html
<!DOCTYPE html>
<html lang="en">
<head>
<meta charset="utf-8">
<title>Total Body Wellness – Patient Pamphlet</title>
<link rel="stylesheet" href="https://fonts.googleapis.com/css2?family=Cinzel:wght@500;600&family=Montserrat:wght@400;500;600;700;800&display=swap">
<style>
  :root{
    --black:#0b0b0b;
    --white:#ffffff;
    --red:#d7141b;
    --ink:#1c1c1c;
    --grey-band:#e6e7e8;
    --row-dark:#e4e5e6;
    --row-light:#f0f0f0;
    --rule:#dcdcdc;
  }
  *{box-sizing:border-box;margin:0;padding:0}
  html,body{width:1200px;height:849px;overflow:hidden;background:var(--white)}
  body{font-family:"Montserrat",sans-serif;color:var(--ink)}
  .pamphlet{position:relative;width:1200px;height:849px;overflow:hidden}
  .abs{position:absolute}

  /* header bands */
  .header{position:absolute;top:0;left:0;width:1200px;height:135px;background:var(--black)}
  .header .red-rule{position:absolute;left:0;right:0;top:123px;height:3px;background:var(--red)}
  .panel-divider{position:absolute;top:0;height:135px;width:1px;background:#222}
  .panel-title{position:absolute;font-family:"Cinzel",serif;font-weight:600;color:var(--white);line-height:1.05;letter-spacing:.5px}
  .panel-sub{font-family:"Cinzel",serif;color:var(--red);font-weight:500;font-size:17px;letter-spacing:.4px;display:block;margin-top:2px}

  .copy{font-size:11.6px;line-height:17px;color:var(--ink)}
  .copy p{margin-bottom:11px}
  .accent{color:var(--red);font-weight:600}

  /* left panel */
  .rule{position:absolute;height:1px;background:var(--rule)}
  .section-head{position:absolute;font-family:"Cinzel",serif;font-weight:600;font-size:16.5px;letter-spacing:.4px}
  .test-table{position:absolute;left:49px;top:419px;width:302px}
  .test-row{display:flex;align-items:center;height:39.5px}
  .test-row:nth-child(odd){background:var(--row-dark)}
  .test-row:nth-child(even){background:var(--row-light)}
  .test-icon{width:33px;height:33px;border-radius:50%;background:var(--black);margin-left:12px;display:flex;align-items:center;justify-content:center}
  .test-num{width:44px;margin-left:20px;color:var(--red);font-weight:800;font-size:17px}
  .test-label{font-weight:600;font-size:11.6px;letter-spacing:.2px}

  .process-band{position:absolute;left:0;top:712px;width:400px;height:137px;background:var(--grey-band)}
  .step{position:absolute;top:732px;width:80px;text-align:center}
  .step-circle{width:49px;height:49px;border:1.4px solid var(--ink);border-radius:50%;margin:0 auto;display:flex;align-items:center;justify-content:center;background:var(--white)}
  .step-label{font-size:8.4px;letter-spacing:.3px;margin-top:9px;color:#333}
  .step-arrow{position:absolute;top:751px;width:0;height:0;border-top:5px solid transparent;border-bottom:5px solid transparent;border-left:6px solid var(--ink)}

  /* middle panel */
  .figure-area{position:absolute;left:523px;top:282px;width:141px;height:403px;border-radius:60px 60px 30px 30px;background:linear-gradient(180deg,#f1dada 0%,#e9c4c4 40%,#efd8d8 100%)}
  .callout{position:absolute;width:95px}
  .callout-icon{position:absolute;width:31px;height:31px;border-radius:50%;background:var(--black);display:flex;align-items:center;justify-content:center}
  .callout h4{color:var(--red);font-weight:600;font-size:8.6px;letter-spacing:.3px;line-height:11px}
  .callout p{font-size:6.6px;line-height:8.7px;margin-top:4px;color:#222}
  .connectors{position:absolute;left:0;top:0}

  .dark-band{position:absolute;top:712px;height:137px;background:var(--black)}
  .bigger-title{position:absolute;left:441px;top:738px;color:var(--red);font-weight:800;font-size:15px;letter-spacing:.3px}
  .bigger-copy{position:absolute;left:441px;top:763px;width:330px;color:var(--white);font-size:8.3px;line-height:11px;font-weight:600}

  .practice-seal{position:absolute;left:636px;top:628px;width:118px;height:118px;border-radius:50%;background:var(--white);border:1.3px solid var(--black);display:flex;flex-direction:column;align-items:center;justify-content:center;text-align:center}
  .practice-seal span{font-size:10px;font-weight:600;letter-spacing:.6px;color:var(--black);line-height:14px}

  /* right panel */
  .service-icon{position:absolute;width:51px;height:51px;border:1.3px solid var(--black);border-radius:50%;display:flex;align-items:center;justify-content:center;background:var(--white)}
  .service{position:absolute;left:910px;width:170px}
  .service .kicker{color:var(--red);font-weight:600;font-size:10px;letter-spacing:.2px;line-height:13px}
  .service h3{font-weight:600;font-size:10px;letter-spacing:.2px;line-height:13px}
  .service p{font-size:8.6px;line-height:13px;margin-top:5px}
  .service ul{list-style:none;margin-top:10px}
  .service li{font-size:8.6px;line-height:13px;padding-left:8px;position:relative;margin-bottom:4px}
  .service li::before{content:"";position:absolute;left:0;top:5px;width:3px;height:3px;border-radius:50%;background:var(--ink)}
  .service .tagline{color:var(--red);font-weight:700;font-size:8.8px;margin-top:12px}
  .product-visual{position:absolute;border-radius:6px}
  .closing{position:absolute;left:857px;top:740px;width:300px;color:var(--white)}
  .closing h3{font-weight:600;font-size:11.6px;line-height:12.5px}
  .closing h3 em{font-style:normal;color:var(--red);font-weight:800}
  .closing p{font-size:7.9px;line-height:11px;margin-top:10px;font-weight:600}
</style>
</head>
<body>
<main class="pamphlet">

  <!-- header -->
  <header class="header">
    <div class="red-rule"></div>
  </header>
  <div class="panel-divider" style="left:400px"></div>
  <div class="panel-divider" style="left:800px"></div>
  <h1 class="panel-title" style="left:49px;top:60px;font-size:27px">BLEEDING IS NOT<br>NORMAL</h1>
  <h1 class="panel-title" style="left:449px;top:60px;font-size:27px">BEYOND THE MOUTH<span class="panel-sub">THE ORAL-SYSTEMIC CONNECTION</span></h1>
  <h1 class="panel-title" style="left:848px;top:62px;font-size:22px">ADVANCED WELLNESS<br>SCREENING IN OUR OFFICE</h1>

  <!-- left panel -->
  <section class="copy abs" style="left:49px;top:153px;width:305px">
    <p>If your gums bleed when you brush or floss, your body is signaling that inflammation is present. Healthy gums should not bleed.</p>
    <p>In many cases, bleeding is caused by harmful bacteria living below the gumline. Left untreated, these pathogens can contribute to chronic inflammation that affects not only your oral health but may also influence your overall health.</p>
    <p>Rather than guessing which bacteria are present, we can identify them through <span class="accent">advanced salivary testing.</span></p>
  </section>
  <div class="rule" style="left:49px;top:370px;width:302px"></div>
  <h2 class="section-head" style="left:49px;top:393px">WHAT WE TEST FOR</h2>

  <div class="test-table">
    <div class="test-row">
      <div class="test-icon"><svg width="18" height="18" viewBox="0 0 18 18" fill="none" stroke="#fff" stroke-width="1"><circle cx="11" cy="6" r="3"/><circle cx="6" cy="12" r="2.5"/><path d="M11 1v2M11 9v2M6 8v1.5M2 12h1.5"/></svg></div>
      <div class="test-num">30</div><div class="test-label">PERIODONTAL PATHOGENS</div>
    </div>
    <div class="test-row">
      <div class="test-icon"><svg width="16" height="18" viewBox="0 0 16 18" fill="none" stroke="#fff" stroke-width="1.3"><path d="M3 2c2-1 3 0 5 0s3-1 5 0 1 6-1 8l-1 6c-1 1-2 0-2-2l-1-3-1 3c0 2-1 3-2 2l-1-6C2 8 1 3 3 2z"/></svg></div>
      <div class="test-num">12</div><div class="test-label">CARIES PATHOGENS</div>
    </div>
    <div class="test-row">
      <div class="test-icon"><svg width="18" height="14" viewBox="0 0 18 14" fill="none" stroke="#fff" stroke-width="1"><path d="M1 10l5-3 4 2 6-6M6 7l-1-4M10 9l1 4M13 6l3 2"/></svg></div>
      <div class="test-num">10</div><div class="test-label">CANDIDA SPECIES</div>
    </div>
    <div class="test-row">
      <div class="test-icon"><svg width="18" height="18" viewBox="0 0 18 18" fill="none" stroke="#fff" stroke-width="1"><circle cx="9" cy="9" r="5"/><circle cx="9" cy="9" r="2"/><path d="M9 1v3M9 14v3M1 9h3M14 9h3M3.5 3.5l2 2M12.5 12.5l2 2M3.5 14.5l2-2M12.5 5.5l2-2"/></svg></div>
      <div class="test-num">7</div><div class="test-label">HERPES VIRUSES</div>
    </div>
  </div>

  <section class="copy abs" style="left:49px;top:604px;width:305px">
    <p style="margin-bottom:14px">This comprehensive analysis allows us to create an individualized whole-mouth disinfection protocol designed specifically for your microbiome.</p>
    <p>Instead of treating every patient the same,<br>we treat <span class="accent">your unique biology.</span></p>
  </section>

  <div class="process-band"></div>
  <div class="step" style="left:34px">
    <div class="step-circle"><svg width="22" height="22" viewBox="0 0 22 22" fill="none" stroke="#1c1c1c" stroke-width="1.3"><path d="M3 2v17h17v-5H8V2z"/></svg></div>
    <div class="step-label">MEASURE</div>
  </div>
  <div class="step-arrow" style="left:117px"></div>
  <div class="step" style="left:118px">
    <div class="step-circle"><svg width="22" height="22" viewBox="0 0 22 22" fill="none" stroke="#1c1c1c" stroke-width="1.3"><circle cx="11" cy="7" r="4.5"/><path d="M2 20c1-5 5-7 9-7s8 2 9 7z"/></svg></div>
    <div class="step-label">PERSONALIZE</div>
  </div>
  <div class="step-arrow" style="left:199px"></div>
  <div class="step" style="left:202px">
    <div class="step-circle"><svg width="20" height="24" viewBox="0 0 20 24" fill="none" stroke="#1c1c1c" stroke-width="1.2"><rect x="5" y="1" width="10" height="4"/><rect x="3" y="5" width="14" height="18" rx="2"/><circle cx="8" cy="12" r="2"/><circle cx="12" cy="17" r="2"/></svg></div>
    <div class="step-label">TREAT</div>
  </div>
  <div class="step-arrow" style="left:283px"></div>
  <div class="step" style="left:286px">
    <div class="step-circle"><svg width="24" height="24" viewBox="0 0 24 24" fill="none" stroke="#1c1c1c" stroke-width="1.4"><path d="M5 14a8 8 0 0 1 12-9M3 5l3 4 4-2"/><rect x="12" y="11" width="6" height="10" rx="2" transform="rotate(30 15 16)"/></svg></div>
    <div class="step-label">RETEST</div>
  </div>

  <!-- middle panel -->
  <section class="copy abs" style="left:449px;top:153px;width:300px;font-size:12px;line-height:17.5px">
    <p style="margin-bottom:16px">Inflammation caused by harmful oral pathogens doesn't stay in your mouth.</p>
    <p>These bacteria, fungi, and viruses can enter the bloodstream and affect your entire body.</p>
  </section>

  <div class="figure-area" role="img" aria-label="Anatomical illustration of a human body showing organs and blood vessels in red"></div>

  <svg class="connectors" width="1200" height="849" fill="none" stroke="#d7141b" stroke-width="0.9">
    <path d="M525 305H581"/>
    <path d="M641 315L600 376"/>
    <path d="M523 415H545L566 378"/>
    <path d="M649 434H608"/>
    <path d="M546 523H552L592 464"/>
    <path d="M649 533H615"/>
  </svg>
  <svg class="connectors" width="1200" height="849" fill="#d7141b">
    <circle cx="581" cy="305" r="1.8"/><circle cx="600" cy="376" r="1.8"/><circle cx="566" cy="378" r="1.8"/>
    <circle cx="608" cy="434" r="1.8"/><circle cx="592" cy="464" r="1.8"/><circle cx="615" cy="533" r="1.8"/>
  </svg>

  <div class="callout-icon" style="left:449px;top:291px"><svg width="16" height="14" viewBox="0 0 16 14" fill="none" stroke="#fff" stroke-width="1"><path d="M4 2c2-2 6-2 8 0 3 1 3 5 1 7-1 2-4 3-6 2-3 1-6-1-6-4 0-2 1-4 3-5z"/></svg></div>
  <div class="callout" style="left:486px;top:299px"><h4>BRAIN</h4><p>Linked to cognitive decline, Alzheimer's disease and stroke risk.</p></div>

  <div class="callout-icon" style="left:649px;top:291px"><svg width="14" height="16" viewBox="0 0 14 16" fill="none" stroke="#fff" stroke-width="1"><path d="M7 15C2 11 1 7 3 4s5-1 4 1c0-2 3-4 4-1 2 3 0 7-4 11z"/></svg></div>
  <div class="callout" style="left:685px;top:299px"><h4>HEART</h4><p>Associated with increased risk of heart disease, inflammation and high blood pressure.</p></div>

  <div class="callout-icon" style="left:449px;top:401px"><svg width="16" height="14" viewBox="0 0 16 14" fill="none" stroke="#fff" stroke-width="1"><path d="M8 1v6M8 5L5 3C2 4 1 9 2 12c2 1 5 0 5-3M8 5l3-2c3 1 4 6 3 9-2 1-5 0-5-3"/></svg></div>
  <div class="callout" style="left:486px;top:410px"><h4>LUNGS</h4><p>Linked to respiratory infections, COPD and worsening lung conditions.</p></div>

  <div class="callout-icon" style="left:649px;top:413px"><svg width="14" height="14" viewBox="0 0 14 14" fill="none" stroke="#fff" stroke-width="1"><path d="M5 2C3 5 1 7 1 9a3 3 0 0 0 6 0c0-2-2-4-2-7zM10 4c-1 2-2 3-2 5a2.5 2.5 0 0 0 5 0c0-2-2-3-3-5z"/></svg></div>
  <div class="callout" style="left:685px;top:422px"><h4>BLOOD SUGAR</h4><p>Associated with insulin resistance and poor diabetes control.</p></div>

  <div class="callout-icon" style="left:449px;top:509px"><svg width="12" height="16" viewBox="0 0 12 16" fill="none" stroke="#fff" stroke-width="1"><circle cx="6" cy="2.5" r="1.6"/><path d="M4 15V8c0-2 1-3 2-3s3 2 3 5H5"/></svg></div>
  <div class="callout" style="left:486px;top:518px"><h4>PREGNANCY</h4><p>Linked to preterm birth, low birth weight and preeclampsia.</p></div>

  <div class="callout-icon" style="left:649px;top:509px"><svg width="16" height="16" viewBox="0 0 16 16" fill="none" stroke="#fff" stroke-width="1"><path d="M2 2l5 5M9 9l5 5"/><circle cx="8" cy="8" r="2"/></svg></div>
  <div class="callout" style="left:685px;top:514px"><h4>JOINTS &amp;<br>IMMUNITY</h4><p>May contribute to arthritis, autoimmune flares and weakened immune response.</p></div>

  <div class="dark-band" style="left:400px;width:400px"></div>
  <div class="practice-seal">
    <span>ELENA R MARSH</span>
    <span>DDS</span>
  </div>
  <h2 class="bigger-title">THE BIGGER PICTURE</h2>
  <p class="bigger-copy">Healthy gums do more than protect your smile. Reducing chronic oral inflammation may also support your heart, brain, lungs, metabolism, immune system and overall well-being.</p>

  <!-- right panel -->
  <div class="product-visual" style="left:1076px;top:167px;width:80px;height:141px;background:linear-gradient(180deg,#1a1a1a 0%,#2a2a2a 45%,#f2f2f2 55%,#ffffff 100%)" role="img" aria-label="Oral cancer screening device with display on a white stand"></div>
  <div class="service-icon" style="left:847px;top:193px"><svg width="26" height="26" viewBox="0 0 26 26" stroke="#d7141b" stroke-width="2.2"><path d="M13 2v22M2 13h22M5 5l16 16M21 5L5 21"/></svg></div>
  <section class="service" style="top:200px">
    <div class="kicker">LUMASCAN®</div>
    <h3>ORAL CANCER SCREENING</h3>
    <p>Advanced fluorescence technology helps detect abnormal cells early, when treatment is most effective.</p>
    <div class="tagline" style="margin-top:13px">Early detection saves lives.</div>
  </section>
  <div class="rule" style="left:848px;top:308px;width:303px"></div>

  <div class="product-visual" style="left:1061px;top:355px;width:100px;height:136px;background:radial-gradient(ellipse at 55% 40%,#2b2b2b 0%,#3a3a3a 35%,#e8e8e8 62%,#ffffff 80%)" role="img" aria-label="Overnight oxygen monitor wristband with finger sensor"></div>
  <div class="service-icon" style="left:847px;top:343px"><svg width="14" height="28" viewBox="0 0 14 28" fill="none" stroke="#1c1c1c" stroke-width="1.4"><path d="M3 2h8M4 2v21a3 3 0 0 0 6 0V2"/><circle cx="7" cy="12" r="1.3"/><circle cx="7" cy="17" r="1.3"/><circle cx="7" cy="22" r="1.3"/></svg></div>
  <section class="service" style="top:345px;width:170px">
    <div class="kicker">COMPLIMENTARY</div>
    <h3>HOME SLEEP SCREENING</h3>
    <p>We have two home overnight oxygen monitors available for you to check out—at no charge.</p>
    <ul>
      <li>Wear the monitor for 2-3 nights</li>
      <li>Painless and easy to use</li>
      <li>We provide a detailed report for you to take to your physician if further evaluation is needed</li>
    </ul>
    <div class="tagline" style="margin-top:8px">Better sleep. Better health.</div>
  </section>
  <div class="rule" style="left:848px;top:551px;width:303px"></div>

  <div class="product-visual" style="left:1078px;top:553px;width:76px;height:158px;background:linear-gradient(90deg,#ffffff 0%,#e4e4e4 35%,#f6f6f6 60%,#dcdcdc 85%,#ffffff 100%)" role="img" aria-label="White DNA double helix"></div>
  <div class="service-icon" style="left:847px;top:581px"><svg width="22" height="26" viewBox="0 0 22 26" fill="none" stroke="#1c1c1c" stroke-width="1.3"><path d="M4 24C6 16 16 10 18 2M4 2c2 8 12 14 14 22M7 6h8M6 13h10M7 20h8"/></svg></div>
  <section class="service" style="top:571px;width:175px">
    <div class="kicker">APOE GENETIC</div>
    <h3>WELLNESS TESTING</h3>
    <p>Understand your inherited genetic variant associated with increased Alzheimer's disease risk so you can take a more personalized approach to your long-term brain health.</p>
  </section>

  <div class="dark-band" style="left:800px;width:400px"></div>
  <section class="closing">
    <h3>Chronic oral inflammation is linked to more than<br><em>70 systemic diseases.</em></h3>
    <p>Your oral health is connected to your total body health. We never stop learning so you can keep living a healthier, longer life.</p>
  </section>

</main>
</body>
</html>
```